Real Estate Webpage Design

We have an existing website: ferndaleestatecollective.com.au
We focus customised service mainly on Property Management and second-hand property sales.
We are not entirely happy about the current design and layout can stay roughly the same as the back end coding is linked to a CRM system.
We would like to see the design are more reachable to our clients and appearing.
Please check our Website Design Draft for more details.

Industry/Entity Type

Real estate Agency

Number of Pages Required

5+ page

Font styles to use
Sans Serif

Colors

Designer to choose colors to be used in the design.

```html
<!DOCTYPE html>
<html lang="en">
<head>
<meta charset="utf-8">
<title>Ferndale Estate Collective</title>
<link href="https://fonts.googleapis.com/css2?family=Poppins:wght@300;400;500;600&display=swap" rel="stylesheet">
<style>
:root{
  --gold:#E9B949;
  --gold-soft:#F6E0AA;
  --cream:#FDF8E6;
  --hero-bg:#EEEFF1;
  --ink:#2F3440;
  --text:#5A5A5A;
  --muted:#9A9A9A;
  --line:#DADADA;
  --white:#FFFFFF;
}
*{box-sizing:border-box;margin:0;padding:0}
html,body{width:1200px;height:2729px;overflow:hidden}
body{position:relative;background:var(--white);font-family:'Poppins',sans-serif;color:var(--text)}
.abs{position:absolute}
a{color:inherit;text-decoration:none}

/* header */
.site-header{left:0;top:0;width:1200px;height:93px;background:var(--white);box-shadow:0 2px 4px rgba(0,0,0,.08);z-index:3}
.brand{display:flex;align-items:center;gap:8px}
.brand-mark{width:26px;height:26px;background:var(--gold);border-radius:3px}
.brand-name{font-weight:600;font-size:25px;color:var(--gold);line-height:1}
.site-header .brand{left:82px;top:38px}
.main-nav{left:432px;top:47px;display:flex;gap:0;font-size:13px;color:#555}
.main-nav a{margin-right:47px}
.btn{display:inline-flex;align-items:center;justify-content:center;background:var(--gold);color:var(--white);border-radius:16px;font-size:13px;font-weight:500}
.header-cta{left:1019px;top:41px;width:93px;height:31px}

/* hero */
.hero{left:0;top:93px;width:1200px;height:582px;background:var(--hero-bg)}
.hero-title{left:87px;top:118px;font-size:42px;font-weight:600;line-height:62px;color:#5B5B5B}
.hero-text{left:87px;top:258px;width:400px;font-size:13.5px;line-height:19px;color:#666}
.hero-tabs{left:87px;top:389px;display:flex}
.hero-tab{width:70px;height:28px;display:flex;align-items:center;justify-content:center;font-size:13px;border-radius:10px 10px 0 0}
.hero-tab.active{background:var(--gold);color:#fff}
.hero-tab.idle{background:#fff;color:var(--gold)}
.search-bar{left:87px;top:417px;width:546px;height:65px;background:#fff;border-radius:0 12px 12px 12px;box-shadow:0 4px 10px rgba(0,0,0,.08);z-index:2}
.search-field{top:14px;font-size:13px;color:#333}
.search-field small{display:block;font-size:12px;color:var(--muted);margin-bottom:5px}
.search-sep{top:22px;width:1px;height:28px;background:var(--line)}
.search-go{left:499px;top:14px;width:41px;height:38px;background:var(--gold);border-radius:8px;display:flex;align-items:center;justify-content:center}
.hero-photo{left:570px;top:13px;width:630px;height:543px;border-radius:90px 0 0 100px;background:linear-gradient(160deg,#cfe3ec 0%,#eef3f5 35%,#b9c0c3 60%,#5f8a4a 82%,#68c3dc 100%)}

/* about */
.about-band{left:0;top:725px;width:463px;height:382px;background:var(--gold-soft);border-radius:0 110px 0 0}
.about-photo{left:87px;top:800px;width:494px;height:370px;border-radius:0 60px 60px 0;background:linear-gradient(170deg,#5a5a58 0%,#9bb2b8 35%,#c9b28f 60%,#6fb7cf 75%,#6b5f56 100%)}
.eyebrow{font-size:13px;color:var(--gold)}
.about-copy{left:641px;top:805px;width:430px}
.about-copy p{font-size:13.5px;line-height:19px;color:#555;margin-top:14px}
.about-copy p + p{margin-top:19px}
.about-copy .btn{width:93px;height:31px;margin-top:30px}

/* listings */
.section-head{left:0;width:1200px;text-align:center}
.section-title{font-size:32px;font-weight:400;color:#555}
.section-title strong{font-weight:600;color:var(--gold)}
.filter-tabs{left:354px;top:1326px;display:flex;font-size:12.5px;color:var(--muted)}
.filter-tabs span{margin-right:62px}
.listing-card{top:1412px;width:289px;height:404px;background:#fff;border-radius:24px;box-shadow:0 3px 10px rgba(0,0,0,.12)}
.listing-photo{left:8px;top:3px;width:273px;height:225px;border-radius:22px}
.listing-rating{left:12px;top:14px;font-size:13px;color:#F2C300;letter-spacing:1px}
.listing-badge{right:10px;top:12px;background:var(--gold);color:#fff;font-size:11px;text-decoration:underline;padding:3px 12px;border-radius:8px}
.listing-price{right:14px;top:200px;color:#fff;font-size:12.5px;text-decoration:underline}
.listing-body{left:10px;top:242px;width:269px;font-size:11.5px;color:#444}
.listing-suburb{display:flex;align-items:center;gap:4px;font-size:12.5px;color:#333}
.listing-addr{font-size:10.5px;margin:2px 0 0 17px}
.listing-feat{display:flex;gap:14px;font-size:9px;margin:6px 0 0 20px;align-items:center}
.listing-feat span{display:flex;align-items:center;gap:2px}
.listing-rent{margin-left:17px;font-size:12.5px;color:#333}
.listing-insp{margin:10px 0 0 21px;font-size:11px;line-height:17px;color:#333}
.listing-divider{left:10px;top:355px;width:269px;height:1px;background:#999}
.listing-actions{left:10px;top:368px;display:flex;gap:11px}
.listing-detail{right:14px;top:367px;width:70px;height:22px;font-size:10px;text-decoration:underline;border-radius:8px}
.see-all{left:556px;top:1843px;width:88px;height:25px;border:1px solid var(--gold);border-radius:13px;color:var(--gold);font-size:12.5px;display:flex;align-items:center;justify-content:center}

/* testimonials */
.testimonials{left:0;top:1906px;width:1200px;height:520px;background:linear-gradient(180deg,#FFFDF3 0%,#FCF5D6 100%)}
.testimonials .section-title{color:var(--ink);font-weight:600}
.testimonials .section-title em{font-style:normal;font-weight:400;color:var(--gold)}
.quote-card{top:2031px;width:305px;height:230px;background:#FFFDF6;border-radius:50px;box-shadow:0 2px 8px rgba(0,0,0,.05)}
.quote-user{left:48px;top:36px;font-size:11px;color:#555}
.quote-stars{display:block;color:#F2C300;font-size:12px;letter-spacing:1px}
.quote-text{left:30px;top:91px;width:250px;font-size:11.5px;line-height:17px;color:#555}
.quote-text u{color:#555}
.dots{left:575px;top:2297px;display:flex;gap:8px}
.dot{width:12px;height:12px;border-radius:50%;background:#fff;box-shadow:0 0 2px rgba(0,0,0,.2)}
.dot.on{background:var(--ink)}

/* footer */
.site-footer{left:0;top:2377px;width:1200px;height:352px;background:#fff;border-radius:0 120px 0 0}
.footer-brand{left:87px;top:2463px;width:230px;text-align:center}
.footer-brand .brand{justify-content:center}
.footer-brand .brand-name{font-size:21px}
.footer-brand h3{font-size:17px;font-weight:500;color:#555;margin-top:12px;line-height:24px}
.footer-brand p{font-size:7.5px;line-height:11px;color:#555;margin:12px 8px 0}
.socials{display:flex;justify-content:center;gap:32px;margin-top:20px}
.socials span{width:15px;height:15px;border:1px solid #555;border-radius:50%}
.footer-nav{left:362px;top:2427px;display:flex;flex-direction:column;gap:12px;font-size:13px;color:#444}
.footer-col{font-size:13px;color:#444;line-height:19px}
.footer-col h4{font-size:13px;font-weight:600;color:#444;margin-bottom:16px}
.footer-map{left:509px;top:2564px;width:343px;height:101px;background:linear-gradient(120deg,#dfe9e1 0%,#eef1f3 50%,#d9e4ec 100%)}
.contact-form{left:874px;top:2441px;width:226px;height:230px;background:#EBECEE;border-radius:14px}
.form-field{left:11px;width:200px;font-size:7.5px;color:#555;border-bottom:1px solid #999;padding-bottom:6px}
.form-send{left:148px;top:210px;width:62px;height:20px;font-size:8px;text-decoration:underline;border-radius:8px}
</style>
</head>
<body>

<header class="abs site-header">
  <div class="abs brand"><span class="brand-mark"></span><span class="brand-name">Ferndale</span></div>
  <nav class="abs main-nav">
    <a>Home</a><a>About Us</a><a>Sell</a><a>buy</a><a>Rent</a><a>Our Team</a><a>Blog</a>
  </nav>
  <a class="abs btn header-cta">Contact Us</a>
</header>

<section class="abs hero">
  <h1 class="abs hero-title">Ferndale – A Place for<br>“The Home”</h1>
  <p class="abs hero-text">Ferndale is named for the quiet, leafy place we all call home, buying a property is one of the most expensive expenses and important assets for people. Ferndale is a real estate company located in Gungahlin, Canberra.</p>
  <div class="abs hero-tabs"><span class="hero-tab active">sell</span><span class="hero-tab idle">buy</span></div>
  <div class="abs hero-photo" role="img" aria-label="Modern white two-storey villa with glass balconies, lawn and pool"></div>
  <form class="abs search-bar">
    <div class="abs search-field" style="left:27px"><small>Location</small>los angelos</div>
    <span class="abs search-sep" style="left:162px"></span>
    <div class="abs search-field" style="left:193px"><small>Proprity Type</small>private housse</div>
    <span class="abs search-sep" style="left:335px"></span>
    <div class="abs search-field" style="left:391px"><small>Price</small>20000$-40000$</div>
    <span class="abs search-go"><svg width="18" height="18" viewBox="0 0 18 18" fill="none" stroke="#333" stroke-width="1.4"><circle cx="9" cy="8" r="6"/><path d="M13 12l3 3"/></svg></span>
  </form>
</section>

<section>
  <div class="abs about-band"></div>
  <div class="abs about-photo" role="img" aria-label="Living room opening onto a poolside terrace with timber cladding"></div>
  <div class="abs about-copy">
    <span class="eyebrow">About Us</span>
    <p>Ferndale is named for the quiet, leafy place we all call home, buying a property is one of the most expensive expenses and important assets for people. Ferndale is a real estate company located in Gungahlin, Canberra.</p>
    <p>Being a portfolio sales agent and property manager, coupled with our high–profile international real estate experience, Ferndale is considered a market leader on the cutting edge with deep industry knowledge, ranging from landlord–tenant relationships, residential purchases.</p>
    <a class="btn">Read More</a>
  </div>
</section>

<section>
  <div class="abs section-head eyebrow" style="top:1236px">Oue Services</div>
  <h2 class="abs section-head section-title" style="top:1268px">This Month At <strong>Ferndale Estate Collective</strong></h2>
  <div class="abs filter-tabs"><span>For Sale</span><span>For Lease</span><span>Open Time</span><span>Sold</span><span>Leased</span></div>

  <article class="abs listing-card" style="left:110px">
    <div class="abs listing-photo" role="img" aria-label="Rooftop infinity pool beside an apartment tower" style="background:linear-gradient(180deg,#9aa6b0 0%,#c9d6de 45%,#2e64a8 70%,#b8693a 100%)"></div>
    <span class="abs listing-rating">★★★<span style="color:#fff">☆☆</span></span>
    <span class="abs listing-badge">For Sale</span>
    <span class="abs listing-price">$500,000+</span>
    <div class="abs listing-body">
      <div class="listing-suburb"><svg width="13" height="13" viewBox="0 0 12 12" fill="none" stroke="#666"><path d="M6 11s4-4 4-6.5a4 4 0 0 0-8 0C2 7 6 11 6 11z"/><circle cx="6" cy="4.5" r="1.4"/></svg>GUNGAHLIN</div>
      <div class="listing-addr">Level 3/12 Banksia Parade Gungahlin ACT</div>
      <div class="listing-feat"><span>▭ 2</span><span>⊔ 2</span><span>⊓ 1</span></div>
      <div class="listing-insp">Next Inspection:<br>Sat 21st May 09:40 AM - 10:00 AM</div>
    </div>
    <span class="abs listing-divider"></span>
    <div class="abs listing-actions">
      <svg width="20" height="18" viewBox="0 0 20 18" fill="none" stroke="#666" stroke-width="1.3"><path d="M10 16S2 11 2 6a4 4 0 0 1 8-1 4 4 0 0 1 8 1c0 5-8 10-8 10z"/></svg>
      <svg width="18" height="18" viewBox="0 0 18 18" fill="none" stroke="#666" stroke-width="1.3"><path d="M4 2h10v14l-5-4-5 4z"/></svg>
      <svg width="20" height="18" viewBox="0 0 20 18" fill="none" stroke="#666" stroke-width="1.3"><rect x="2" y="3" width="16" height="12" rx="3"/><path d="M3 5l7 5 7-5"/></svg>
      <svg width="19" height="18" viewBox="0 0 20 19" fill="none" stroke="#666" stroke-width="1.3"><path d="M10 1l2.6 5.6 6 .6-4.5 4 1.3 6L10 14l-5.4 3.2 1.3-6-4.5-4 6-.6z"/></svg>
    </div>
    <a class="abs btn listing-detail">View Detail</a>
  </article>

  <article class="abs listing-card" style="left:455px">
    <div class="abs listing-photo" role="img" aria-label="White apartment block with red balconies and a large tree" style="background:linear-gradient(170deg,#3d7fd0 0%,#dfe5ea 40%,#c96a7a 60%,#3e4a2e 85%,#555 100%)"></div>
    <span class="abs listing-rating">★★★<span style="color:#fff">☆☆</span></span>
    <span class="abs listing-badge">For Sale</span>
    <span class="abs listing-price">$389,900+</span>
    <div class="abs listing-body">
      <div class="listing-suburb"><svg width="13" height="13" viewBox="0 0 12 12" fill="none" stroke="#666"><path d="M6 11s4-4 4-6.5a4 4 0 0 0-8 0C2 7 6 11 6 11z"/><circle cx="6" cy="4.5" r="1.4"/></svg>BELCONNEN</div>
      <div class="listing-addr">88/20 Orchard Lane Belconnen</div>
      <div class="listing-feat"><span>▭ 1</span><span>⊔ 1</span><span>⊓ 1</span></div>
      <div class="listing-insp">Next Inspection:<br>Sat 21st May 09:40 AM - 10:00 AM</div>
    </div>
    <span class="abs listing-divider"></span>
    <div class="abs listing-actions">
      <svg width="20" height="18" viewBox="0 0 20 18" fill="none" stroke="#666" stroke-width="1.3"><path d="M10 16S2 11 2 6a4 4 0 0 1 8-1 4 4 0 0 1 8 1c0 5-8 10-8 10z"/></svg>
      <svg width="18" height="18" viewBox="0 0 18 18" fill="none" stroke="#666" stroke-width="1.3"><path d="M4 2h10v14l-5-4-5 4z"/></svg>
      <svg width="20" height="18" viewBox="0 0 20 18" fill="none" stroke="#666" stroke-width="1.3"><rect x="2" y="3" width="16" height="12" rx="3"/><path d="M3 5l7 5 7-5"/></svg>
      <svg width="19" height="18" viewBox="0 0 20 19" fill="none" stroke="#666" stroke-width="1.3"><path d="M10 1l2.6 5.6 6 .6-4.5 4 1.3 6L10 14l-5.4 3.2 1.3-6-4.5-4 6-.6z"/></svg>
    </div>
    <a class="abs btn listing-detail">View Detail</a>
  </article>

  <article class="abs listing-card" style="left:801px">
    <div class="abs listing-photo" role="img" aria-label="Empty open-plan living area with timber floor and staircase" style="background:linear-gradient(180deg,#e8e8e8 0%,#d6d6d4 50%,#a89c8c 100%)"></div>
    <span class="abs listing-rating">★★★<span style="color:#fff">☆☆</span></span>
    <span class="abs listing-badge">For Lease</span>
    <div class="abs listing-body">
      <div class="listing-suburb"><svg width="13" height="13" viewBox="0 0 12 12" fill="none" stroke="#666"><path d="M6 11s4-4 4-6.5a4 4 0 0 0-8 0C2 7 6 11 6 11z"/><circle cx="6" cy="4.5" r="1.4"/></svg>LAWSON</div>
      <div class="listing-addr">14/9 Kestrel Terrace Lawson</div>
      <div class="listing-feat" style="margin-left:17px"><span>▭ 3</span><span>⊔ 2</span><span>⊓ 2</span></div>
      <div class="listing-rent">$640 - $660 per week</div>
      <div class="listing-insp" style="margin-top:4px;margin-left:17px">Next Inspection:<br>Sat 21st May 02:30 PM - 02:45 PM</div>
    </div>
    <span class="abs listing-divider"></span>
    <div class="abs listing-actions">
      <svg width="20" height="18" viewBox="0 0 20 18" fill="none" stroke="#666" stroke-width="1.3"><path d="M10 16S2 11 2 6a4 4 0 0 1 8-1 4 4 0 0 1 8 1c0 5-8 10-8 10z"/></svg>
      <svg width="18" height="18" viewBox="0 0 18 18" fill="none" stroke="#666" stroke-width="1.3"><path d="M4 2h10v14l-5-4-5 4z"/></svg>
      <svg width="20" height="18" viewBox="0 0 20 18" fill="none" stroke="#666" stroke-width="1.3"><rect x="2" y="3" width="16" height="12" rx="3"/><path d="M3 5l7 5 7-5"/></svg>
      <svg width="19" height="18" viewBox="0 0 20 19" fill="none" stroke="#666" stroke-width="1.3"><path d="M10 1l2.6 5.6 6 .6-4.5 4 1.3 6L10 14l-5.4 3.2 1.3-6-4.5-4 6-.6z"/></svg>
    </div>
    <a class="abs btn listing-detail">View Detail</a>
  </article>

  <a class="abs see-all">See All</a>
</section>

<section class="abs testimonials"></section>
<div class="abs section-head eyebrow" style="top:1942px;left:-10px;font-size:12px">Testimonials</div>
<h2 class="abs section-head section-title testimonials-title" style="top:1960px;left:-10px;color:var(--ink);font-weight:600">What they are saying <span style="font-weight:400;color:var(--gold)">about us</span></h2>

<article class="abs quote-card" style="left:93px">
  <div class="abs quote-user">@mira_l<span class="quote-stars">★★★★★</span></div>
  <p class="abs quote-text">Very good service. Our porperty manager is very responsible, prompting and cares about detail. They use system to track evrything so no need to worry about miscommunication.<br>I strongly recommend this agent.</p>
</article>
<article class="abs quote-card" style="left:448px">
  <div class="abs quote-user" style="top:31px">@nessa<span class="quote-stars">★★★☆☆</span></div>
  <p class="abs quote-text" style="left:38px">I would highly recommend Ferndale property to you, they were helping me to manage my investment property, they found a quality teants in 2 days and maintain my property in a really good condition......<u>read more</u></p>
</article>
<article class="abs quote-card" style="left:803px">
  <div class="abs quote-user" style="top:31px">@tkwan<span class="quote-stars">★★★★☆</span></div>
  <p class="abs quote-text" style="left:33px">Louise is My best property manager! Always happy to response my queries keep us well informed at all stage.<br>I well definitely recommend her to my frinds</p>
</article>
<div class="abs dots"><span class="dot"></span><span class="dot on"></span><span class="dot"></span></div>

<footer class="abs site-footer"></footer>
<div class="abs footer-brand">
  <div class="brand"><span class="brand-mark" style="width:22px;height:22px"></span><span class="brand-name">Ferndale</span></div>
  <h3>Ferndale – A Place for “The Home”</h3>
  <p>Ferndale is named for the quiet, leafy place we call home, buying a property is one of the most expensive expenses and important assets for people. Ferndale is a real estate company located in Gungahlin, Canberra.</p>
  <div class="socials"><span></span><span></span><span></span></div>
</div>
<nav class="abs footer-nav">
  <a>Home</a><a>About Us</a><a>Sell</a><a>buy</a><a>Rent</a><a>Our Team</a><a>Blog</a><a>Contact Us</a>
</nav>
<div class="abs footer-col" style="left:503px;top:2418px;width:160px">
  <h4 style="margin-left:15px">Locate Us</h4>
  <div style="display:flex;gap:3px"><svg width="13" height="14" viewBox="0 0 12 12" fill="none" stroke="#666"><path d="M6 11s4-4 4-6.5a4 4 0 0 0-8 0C2 7 6 11 6 11z"/><circle cx="6" cy="4.5" r="1.4"/></svg><span style="font-size:12px;line-height:17px">118/4 Wattle Crest Rd, Gungahlin, ACT, 2915</span></div>
  <div style="display:flex;gap:3px;margin-top:14px"><svg width="13" height="14" viewBox="0 0 14 14" fill="none" stroke="#666"><path d="M3 1l3 3-2 2a8 8 0 0 0 4 4l2-2 3 3-2 2C6 13 1 8 1 3z"/></svg><span style="font-size:12px;line-height:17px">P: 02 5550 1934<br>F: 02 5550 2067</span></div>
</div>
<div class="abs footer-map" role="img" aria-label="Street map showing the office location"></div>
<div class="abs footer-col" style="left:691px;top:2418px">
  <h4>Trading hours</h4>
  <p>Monday – Friday<br>8:30 am – 5:00pm<br>Weekend – Closed<br>Public holiday – Closed<br>After hour by appointment</p>
</div>
<div class="abs footer-col" style="left:884px;top:2418px"><h4>Contact Us</h4></div>
<form class="abs contact-form">
  <div class="abs form-field" style="top:18px">First Name</div>
  <div class="abs form-field" style="top:50px">Name</div>
  <div class="abs form-field" style="top:85px">Email</div>
  <div class="abs form-field" style="top:120px">Phone</div>
  <div class="abs form-field" style="top:155px;padding-bottom:26px">Message</div>
  <a class="abs btn form-send">Send Email</a>
</form>

</body>
</html>
```